Flyer for the Lumen 2025 Conference

I am looking to produce a flyer for our upcoming conference, Lumen 2025. This is an annual conference that we plan to publicize on social media. The ideal designer will create a flyer that is eye-catching and effectively communicates the key information. Please see attached our logo, speaker photo, and flyer content.

Target Market(s)

All demographics

Industry/Entity Type

Christian

Font styles to use
Sans Serif

Requirements
Should not have
• Cross, church

```html
<!DOCTYPE html>
<html lang="en">
<head>
<meta charset="utf-8">
<title>Lumen 2025 Conference Flyer</title>
<link href="https://fonts.googleapis.com/css2?family=Oswald:wght@500;600&family=Montserrat:wght@400&family=Quicksand:wght@400&display=swap" rel="stylesheet">
<style>
  :root{
    --black:#000000;
    --navy:#023a66;
    --suit:#1f66b8;
    --orange:#f39a1e;
    --white:#ffffff;
  }
  *{margin:0;padding:0;box-sizing:border-box}
  html,body{width:1200px;height:768px;overflow:hidden;background:var(--navy)}
  .flyer{position:relative;width:1200px;height:768px;background:var(--navy);overflow:hidden;font-family:"Oswald",sans-serif;color:var(--white)}
  .top-band{position:absolute;left:0;top:0;width:1200px;height:330px;background:var(--black)}
  .speaker-photo{position:absolute;left:23px;top:22px;width:530px;height:680px;
    background:radial-gradient(ellipse closest-side at 55% 50%, var(--suit) 0%, #15508f 50%, rgba(2,58,102,0) 100%);}
  .speaker-caption{position:absolute;left:20px;width:450px;text-align:center;font-family:"Quicksand",sans-serif;font-style:italic;color:var(--orange);line-height:1;white-space:nowrap}
  .speaker-role{top:654px;font-size:40px}
  .speaker-name{top:698px;font-size:40px}
  .event-title{position:absolute;left:480px;top:52px;font-size:46px;font-weight:500;line-height:51px}
  .brand-box{position:absolute;left:982px;top:27px;width:165px;height:164px;background:var(--navy);border:4px solid var(--white);display:flex;align-items:center;justify-content:center}
  .brand-name{font-family:"Oswald",sans-serif;font-weight:500;font-size:42px;color:var(--white);letter-spacing:1px}
  .topic-label{position:absolute;left:480px;top:190px;font-size:34px;font-weight:600;letter-spacing:29px;line-height:1}
  .topic-title{position:absolute;left:479px;top:228px;font-size:76px;font-weight:600;line-height:1.1;white-space:nowrap}
  .session{position:absolute;top:342px;width:208px;height:130px;border-radius:0 0 22px 22px;background:linear-gradient(180deg,#041a2e 0%,var(--black) 100%)}
  .session svg{position:absolute;left:20px}
  .session .ico-cal{top:25px}
  .session .ico-clock{top:75px}
  .session-day{position:absolute;left:58px;top:14px;font-size:30px;font-weight:500;color:var(--orange);line-height:1.1}
  .session-date,.session-time{position:absolute;left:58px;font-size:20px;font-weight:500;line-height:1;white-space:nowrap}
  .session-date{top:60px}
  .session-time{top:85px}
  .venue{position:absolute;left:648px;top:524px;display:flex;gap:10px;align-items:flex-start}
  .venue-text{font-size:17px;font-weight:500;line-height:21px;width:390px}
  .app-note{position:absolute;left:529px;top:655px;font-family:"Montserrat",sans-serif;font-size:18.5px;line-height:21px;color:var(--orange)}
  .store-badge{position:absolute;top:658px;width:138px;height:38px;background:var(--black);border:1.5px solid #bdbdbd;border-radius:6px}
  .contact-row{position:absolute;left:528px;top:712px;height:38px;display:flex;align-items:center;font-family:"Montserrat",sans-serif;font-size:18.5px;white-space:nowrap}
  .contact-item{display:flex;align-items:center;gap:5px}
  .divider{width:2px;height:38px;background:var(--white);margin:0 10px}
</style>
</head>
<body>
<div class="flyer">
  <div class="top-band"></div>

  <div class="speaker-photo" role="img" aria-label="Portrait photo of the speaker seated in a bright blue suit"></div>
  <p class="speaker-caption speaker-role">Speaker</p>
  <p class="speaker-caption speaker-name">Prophet Samuel Okoro</p>

  <h1 class="event-title">LUMEN 2025<br>A PropheticConference</h1>

  <div class="brand-box"><span class="brand-name">SELAH</span></div>

  <p class="topic-label">TOPIC</p>
  <h2 class="topic-title">The Voice Of The Lord</h2>

  <div class="session" style="left:517px">
    <svg class="ico-cal" width="24" height="24" viewBox="0 0 24 24" fill="none" stroke="#f39a1e" stroke-width="2"><rect x="3" y="5" width="18" height="16" rx="2"/><path d="M3 10h18M8 3v4M16 3v4M7 14h2M11 14h2M15 14h2M7 17h2M11 17h2"/></svg>
    <svg class="ico-clock" width="24" height="24" viewBox="0 0 24 24" fill="none" stroke="#f39a1e" stroke-width="2"><circle cx="12" cy="12" r="9"/><path d="M12 7v5l3 3"/></svg>
    <span class="session-day">Friday</span>
    <span class="session-date">December 26th</span>
    <span class="session-time">6:30PM - 9:00PM</span>
  </div>
  <div class="session" style="left:737px">
    <svg class="ico-cal" width="24" height="24" viewBox="0 0 24 24" fill="none" stroke="#f39a1e" stroke-width="2"><rect x="3" y="5" width="18" height="16" rx="2"/><path d="M3 10h18M8 3v4M16 3v4M7 14h2M11 14h2M15 14h2M7 17h2M11 17h2"/></svg>
    <svg class="ico-clock" width="24" height="24" viewBox="0 0 24 24" fill="none" stroke="#f39a1e" stroke-width="2"><circle cx="12" cy="12" r="9"/><path d="M12 7v5l3 3"/></svg>
    <span class="session-day">Saturday</span>
    <span class="session-date">December 27th</span>
    <span class="session-time">5:30PM &nbsp;- 8:00PM</span>
  </div>
  <div class="session" style="left:956px">
    <svg class="ico-cal" width="24" height="24" viewBox="0 0 24 24" fill="none" stroke="#f39a1e" stroke-width="2"><rect x="3" y="5" width="18" height="16" rx="2"/><path d="M3 10h18M8 3v4M16 3v4M7 14h2M11 14h2M15 14h2M7 17h2M11 17h2"/></svg>
    <svg class="ico-clock" width="24" height="24" viewBox="0 0 24 24" fill="none" stroke="#f39a1e" stroke-width="2"><circle cx="12" cy="12" r="9"/><path d="M12 7v5l3 3"/></svg>
    <span class="session-day">Sunday</span>
    <span class="session-date">December 29th</span>
    <span class="session-time">4:30PM - 7:00PM</span>
  </div>

  <div class="venue">
    <svg width="26" height="34" viewBox="0 0 26 34" fill="none" stroke="#f39a1e" stroke-width="2.5"><path d="M13 32C13 32 2 20 2 12a11 11 0 0 1 22 0c0 8-11 20-11 20z"/><circle cx="13" cy="12" r="4"/></svg>
    <p class="venue-text">The Harborview Performing Arts Center 215 Linden Street Fairhaven, Maine 04110</p>
  </div>

  <p class="app-note">Download the Selah App<br>to stay updated on the event</p>
  <div class="store-badge" style="left:820px"></div>
  <div class="store-badge" style="left:969px"></div>

  <div class="contact-row">
    <span class="contact-item">
      <svg width="18" height="18" viewBox="0 0 24 24" fill="#f39a1e"><path d="M6.6 10.8a15 15 0 0 0 6.6 6.6l2.2-2.2a1 1 0 0 1 1-.25 11.4 11.4 0 0 0 3.6.57 1 1 0 0 1 1 1V20a1 1 0 0 1-1 1A17 17 0 0 1 3 4a1 1 0 0 1 1-1h3.5a1 1 0 0 1 1 1c0 1.25.2 2.45.57 3.6a1 1 0 0 1-.25 1z"/></svg>
      555 014 2290
    </span>
    <span class="divider"></span>
    <span class="contact-item">
      <svg width="20" height="16" viewBox="0 0 24 18" fill="none" stroke="#f39a1e" stroke-width="2"><rect x="2" y="2" width="20" height="14" rx="1"/><path d="M2 3l10 7 10-7"/></svg>
      contact@selahvoice.org
    </span>
    <span class="divider"></span>
    <span class="contact-item">
      <svg width="20" height="20" viewBox="0 0 24 24" fill="none" stroke="#f39a1e" stroke-width="1.8"><circle cx="12" cy="12" r="9"/><path d="M3 12h18M12 3c3 3 3 15 0 18M12 3c-3 3-3 15 0 18"/></svg>
      www.selahvoice.org
    </span>
  </div>
</div>
</body>
</html>
```